Automotive Accessories Business Card

Design a business template that match our new logo design and our industry.

https://www.qelmotorgear.com/

Target Market(s)

Aftermarket auto parts and accessories

Industry/Entity Type

automotive

Contact Information for Business Card

company logo

Font styles to use
Serif
Sans Serif

Colors
EB3D1F
EC4F4E
F09395
F8D3D4
FCEDEE

```html
<!DOCTYPE html>
<html lang="en">
<head>
<meta charset="utf-8">
<title>QEL Motor Gear – Business Card</title>
<link rel="stylesheet" href="https://fonts.googleapis.com/css2?family=Montserrat:wght@400;500;700;800&display=swap">
<style>
  :root {
    --stage: #e9e9e9;
    --card: #3d3d3e;
    --red: #d41f27;
    --white: #ffffff;
    --muted: #f2f2f2;
  }
  * { box-sizing: border-box; margin: 0; padding: 0; }
  html, body { width: 1200px; height: 802px; overflow: hidden; }
  body {
    background: var(--stage);
    font-family: "Montserrat", Arial, sans-serif;
    display: flex;
    align-items: center;
    justify-content: center;
    gap: 40px;
  }
  .card {
    position: relative;
    width: 520px;
    height: 298px;
    background: var(--card);
    overflow: hidden;
    box-shadow: 0 6px 18px rgba(0,0,0,.18);
  }
  /* front */
  .corner-tab {
    position: absolute; top: 0; right: 0;
    width: 22px; height: 26px;
    background: var(--red);
    border-bottom-left-radius: 4px;
  }
  .person {
    position: absolute; top: 26px; right: 36px;
    text-align: right;
  }
  .person-name {
    color: var(--red);
    font-weight: 800;
    font-size: 17px;
    letter-spacing: 2.5px;
    text-transform: uppercase;
  }
  .person-role {
    color: var(--white);
    font-size: 12px;
    font-weight: 500;
    margin-top: 2px;
  }
  .brand {
    display: flex;
    align-items: center;
    gap: 10px;
  }
  .brand-mark {
    width: 18px; height: 18px;
    background: var(--red);
    flex: none;
  }
  .brand-name {
    color: var(--white);
    font-weight: 800;
    text-transform: uppercase;
    letter-spacing: 1px;
    white-space: nowrap;
  }
  .front .brand { position: absolute; left: 38px; top: 104px; }
  .front .brand-name { font-size: 24px; }
  .contacts {
    position: absolute; left: 38px; top: 160px;
    list-style: none;
    color: var(--white);
    font-size: 13px;
    line-height: 21px;
  }
  .contacts li { display: flex; align-items: center; gap: 9px; }
  .contacts svg { width: 11px; height: 11px; fill: var(--red); flex: none; }
  .address-band {
    position: absolute; left: 0; bottom: 0;
    width: 520px; height: 44px;
  }
  .address-band svg { position: absolute; inset: 0; }
  .address {
    position: absolute; left: 38px; bottom: 9px;
    color: var(--white);
    font-size: 13px;
    font-weight: 500;
  }
  /* back */
  .back .brand {
    position: absolute; left: 50%; top: 50%;
    transform: translate(-50%, -50%);
    gap: 12px;
  }
  .back .brand-mark { width: 22px; height: 22px; }
  .back .brand-name { font-size: 30px; }
</style>
</head>
<body>

<section class="card front" aria-label="Business card front">
  <div class="corner-tab"></div>
  <div class="person">
    <p class="person-name">Daniel Corwin</p>
    <p class="person-role">Manager</p>
  </div>

  <div class="brand">
    <span class="brand-mark"></span>
    <span class="brand-name">QEL Motor Gear Inc</span>
  </div>

  <ul class="contacts">
    <li>
      <svg viewBox="0 0 24 24" aria-hidden="true"><path d="M6.6 10.8a15.1 15.1 0 0 0 6.6 6.6l2.2-2.2a1 1 0 0 1 1-.25 11.4 11.4 0 0 0 3.6.57 1 1 0 0 1 1 1V20a1 1 0 0 1-1 1A17 17 0 0 1 3 4a1 1 0 0 1 1-1h3.5a1 1 0 0 1 1 1c0 1.25.2 2.45.57 3.6a1 1 0 0 1-.25 1z"/></svg>
      1-866-555-0142
    </li>
    <li>
      <svg viewBox="0 0 24 24" aria-hidden="true"><path d="M2 5h20v14H2zm2 2v.5l8 5 8-5V7z"/></svg>
      sales@qelmotorgear.com
    </li>
    <li>
      <svg viewBox="0 0 24 24" aria-hidden="true"><circle cx="12" cy="12" r="10"/></svg>
      www.qelmotorgear.com
    </li>
  </ul>

  <div class="address-band">
    <svg viewBox="0 0 520 44" preserveAspectRatio="none" aria-hidden="true">
      <polygon points="0,10 360,10 372,0 520,0 520,14 380,14 368,24 368,44 0,44" fill="var(--red)"/>
    </svg>
    <p class="address">240 W. Harbor Ave, Unit B, Riverton, CA 92507</p>
  </div>
</section>

<section class="card back" aria-label="Business card back">
  <div class="brand">
    <span class="brand-mark"></span>
    <span class="brand-name">QEL Motor Gear Inc</span>
  </div>
</section>

</body>
</html>
```